Roofing Company Modern look

I want a modern and sophisticated look for our roofing business.

Our address is :

5217 Mallow Creek Ln
Orlando, Fl 32825

(407)-583-2196

www.HarborlineRoofsFl.com

I also want to make sure on the back there is a spot to put
Project Manager Name :

Number:

Because the cards will be used by all sales people

Project Manager Name :

Also there are accreditation we have logos are uploaded here as well that I would like maybe on the back of card as well

I also want to highlight our special attributions or trades:

Residential & Commercial
Fully Insured
License # CCC7482913
Insurance Claims
Serving Central Florida Since 1992
Free Estimates

Contact Information for Business Card

Our address is :

5217 Mallow Creek Ln
Orlando, Fl 32825

(407)-583-2196

Project Manager Name :

Residential & Commercial
Fully Insured
License # CCC7482913
Insurance Claims
Free Estimates

Font styles to use
Serif
Sans Serif

Colors
3176b5

Requirements
Must have
• Must have royal blue like my logo grey and black are the colors I like

```html
<!DOCTYPE html>
<html lang="en">
<head>
<meta charset="utf-8">
<title>Harborline Roofing &amp; Gutters – Business Card</title>
<link href="https://fonts.googleapis.com/css2?family=Arimo:wght@400;700&display=swap" rel="stylesheet">
<style>
  :root {
    --backdrop: #1c1816;
    --card: #121212;
    --royal-blue: #3176b5;
    --blue-light: #3d9be3;
    --blue-dark: #1558b0;
    --grey-text: #c9c9c9;
    --grey-rule: #4a4a4a;
    --grey-label: #9a9a9a;
  }
  * { box-sizing: border-box; margin: 0; padding: 0; }
  html, body {
    width: 1200px; height: 842px; overflow: hidden;
    background: var(--backdrop);
    font-family: "Arimo", Arial, sans-serif;
  }
  .stage {
    position: relative; width: 1200px; height: 842px;
    display: flex; align-items: center; justify-content: center; gap: 48px;
  }
  .card {
    position: relative; width: 540px; height: 309px;
    background: var(--card);
    box-shadow: 0 14px 30px rgba(0,0,0,.55);
    overflow: hidden;
  }
  .band {
    position: absolute; left: 0; right: 0; height: 13px;
    background: linear-gradient(90deg, var(--blue-dark), var(--blue-light) 55%, var(--blue-dark));
  }
  .band--top { top: 0; }
  .band--bottom { bottom: 14px; }

  /* front */
  .front-content {
    position: absolute; inset: 36px 0 40px 0;
    display: flex; flex-direction: column; align-items: center; text-align: center;
  }
  .brand { display: flex; align-items: center; gap: 12px; margin-bottom: 16px; }
  .brand-dot { width: 38px; height: 38px; border-radius: 50%; background: var(--royal-blue); }
  .brand-name {
    font-weight: 700; font-size: 19px; letter-spacing: 1px;
    color: var(--blue-light); text-transform: uppercase; line-height: 1.15; text-align: left;
  }
  .person-name {
    font-weight: 700; font-size: 24px; color: var(--royal-blue);
    letter-spacing: .5px; text-transform: uppercase;
  }
  .rule { width: 120px; height: 1px; background: var(--grey-rule); margin: 8px 0; }
  .address, .contact { font-size: 17px; color: var(--grey-text); line-height: 1.25; }

  /* back */
  .tab {
    position: absolute; width: 10px; height: 52px;
    background: linear-gradient(180deg, var(--blue-dark), var(--blue-light));
    border-right: 3px solid #8a8a8a;
  }
  .tab--left { left: 0; top: 170px; }
  .tab--right { right: 0; top: 52px; border-right: none; border-left: 3px solid #8a8a8a; }
  .attributes {
    position: absolute; top: 22px; left: 0; right: 0;
    text-align: center; list-style: none;
    font-size: 15px; line-height: 1.3; color: var(--grey-text);
  }
  .manager-fields {
    position: absolute; top: 150px; left: 110px; right: 110px;
    display: flex; flex-direction: column; gap: 9px;
  }
  .field {
    display: flex; align-items: flex-end; gap: 8px;
    font-size: 12px; color: var(--grey-label); white-space: nowrap;
  }
  .field-line { flex: 1; height: 1px; background: var(--grey-rule); margin-bottom: 2px; }
  .badges {
    position: absolute; bottom: 22px; left: 0; right: 0;
    display: flex; justify-content: center; align-items: center; gap: 30px;
  }
</style>
</head>
<body>
<main class="stage">

  <section class="card card--front" aria-label="Business card front">
    <div class="band band--top"></div>
    <div class="front-content">
      <div class="brand">
        <span class="brand-dot"></span>
        <span class="brand-name">Harborline<br>Roofing &amp; Gutters LLC</span>
      </div>
      <p class="person-name">Marcus Delaney</p>
      <div class="rule"></div>
      <p class="address">5217 Mallow Creek Ln<br>Orlando, Fl 32825</p>
      <div class="rule"></div>
      <p class="contact">(407)-583-2196<br>www.HarborlineRoofsFl.com</p>
    </div>
    <div class="band band--bottom"></div>
  </section>

  <section class="card card--back" aria-label="Business card back">
    <div class="tab tab--left"></div>
    <div class="tab tab--right"></div>
    <ul class="attributes">
      <li>Residential &amp; Commercial</li>
      <li>Fully Insured</li>
      <li>License # CCC7482913</li>
      <li>Insurance Claims</li>
      <li>Serving Central Florida Since 1992</li>
      <li>Free Estimates</li>
    </ul>
    <div class="manager-fields">
      <p class="field"><span>Project Manager Name:</span><span class="field-line"></span></p>
      <p class="field"><span>Number:</span><span class="field-line"></span></p>
    </div>
    <div class="badges">
      <svg width="64" height="50" viewBox="0 0 72 56" role="img" aria-label="Shingle applicator certification badge">
        <polygon points="36,2 70,28 36,54 2,28" fill="#1f4f9a"/>
      </svg>
      <svg width="54" height="54" viewBox="0 0 64 64" role="img" aria-label="Screened and approved listing badge">
        <circle cx="32" cy="32" r="30" fill="#9aa3ab"/>
      </svg>
      <svg width="84" height="36" viewBox="0 0 90 40" role="img" aria-label="Authorized roofing contractor badge">
        <rect x="1" y="1" width="88" height="38" fill="#e8e8e8"/>
      </svg>
      <svg width="46" height="54" viewBox="0 0 52 60" role="img" aria-label="Accredited business rating badge">
        <rect x="1" y="1" width="50" height="58" rx="6" fill="#1f5a9a"/>
      </svg>
    </div>
  </section>

</main>
</body>
</html>
```